High-end construction company needs a business card design

We need a modern looking business card that draws people in, is memorable and looks so good people will want to sick it on their fridges.
On the first side what is needed are:
Logo
My name - Tomasz Brelwik
Title - Managing Director
Website - www.varkelt.co.uk
Email - tomasz@varkelt.co.uk
Telephone - 020 5194 6281
Mobile - 07845139072
On the back side was is needed is a list of all the services we provide:
-Kitchen Renovations
-Bathroom Renovations
-House Renovations
-Garage Conversions
-Extensions
-Loft Conversions
-Conservatories
-Carpentry
-Tiling
-Electrical
-Plumbing & Heating
-Bricklaying
-Landscaping
-Decorating
-Plastering
We would like the colours to be the same shades as on the logo with grey or black for the words.
Target Market(s)
Anyone who needs building work done
Contact Information for Business Card
This business card is for a construction company which strives to deliver excellent service and quality.
The look and feel of the card should represent this.
Requirements
Must have
- On the first side what is needed are:
Logo
My name - Tomasz Brelwik
Title - Managing Director
Website - www.varkelt.co.uk
Email - tomasz@varkelt.co.uk
Telephone - 020 5194 6281
Mobile - 07845139072
Nice to have
- Cool looking features

```html
<!DOCTYPE html>
<html lang="en">
<head>
<meta charset="utf-8">
<title>Varkelt Construction Ltd – Business Card</title>
<link href="https://fonts.googleapis.com/css2?family=Open+Sans:wght@400;600;700&display=swap" rel="stylesheet">
<style>
  :root {
    --page: #8b8c8b;
    --card: #ececee;
    --green-dark: #3b7d35;
    --green-light: #5cab3c;
    --green-pale: #8cc66e;
    --ink: #454545;
    --white: #ffffff;
  }
  * { margin: 0; padding: 0; box-sizing: border-box; }
  html, body {
    width: 1200px; height: 900px; overflow: hidden;
    background: var(--page);
    font-family: "Open Sans", sans-serif;
  }
  .card {
    position: absolute; left: 358px; width: 453px; height: 251px;
    background: var(--card); overflow: hidden;
  }
  .card--front { top: 163px; }
  .card--back { top: 467px; }

  .brand {
    position: absolute; color: var(--green-light); font-weight: 700;
    text-align: center; line-height: 1;
  }
  .brand__name { display: block; font-size: 31px; letter-spacing: 0.5px; }
  .brand__sub { display: block; font-size: 8.6px; letter-spacing: 1.6px; margin-top: 5px; }
  .card--front .brand { left: 56px; top: 112px; width: 156px; }
  .card--back .brand { left: 148px; top: 60px; width: 156px; }

  .skyline {
    position: absolute; left: 262px; top: 92px; width: 191px; height: 128px;
    background: linear-gradient(180deg, rgba(200,205,200,0) 0%, rgba(200,205,200,0.45) 60%, rgba(200,205,200,0.25) 100%);
  }
  .divider {
    position: absolute; left: 226px; top: 83px; width: 1px; height: 85px;
    background: var(--green-light);
  }
  .person { position: absolute; left: 247px; top: 84px; }
  .person__name { font-size: 14px; font-weight: 700; color: var(--green-light); line-height: 1.2; }
  .person__title { font-size: 10.5px; color: var(--ink); line-height: 1.2; }
  .contacts { position: absolute; left: 252px; top: 128px; list-style: none; }
  .contacts li {
    display: flex; align-items: center; gap: 6px;
    font-size: 10.5px; color: var(--ink); line-height: 12.7px;
  }
  .contacts svg { width: 8px; height: 8px; fill: var(--green-light); flex: none; }

  .wave { position: absolute; left: 0; bottom: 0; width: 453px; height: 60px; }
  .website {
    position: absolute; left: 299px; top: 226px;
    font-size: 10.5px; color: var(--white); letter-spacing: 0.4px;
  }
  .website span { color: var(--green-pale); }

  .services-rule {
    position: absolute; left: 0; top: 134px; width: 100%; height: 1.5px;
    background: var(--green-light);
  }
  .services-band {
    position: absolute; left: 0; top: 138px; width: 100%; height: 113px;
    background: var(--green-dark);
  }
  .services-tab {
    position: absolute; left: 172px; top: 131px; width: 115px; height: 25px;
    background: var(--green-light); border: 1.5px solid var(--white);
    border-top: none; border-radius: 0 0 4px 4px;
    color: var(--white); font-size: 10.5px; font-weight: 600;
    letter-spacing: 2.4px; text-align: center; line-height: 23px;
  }
  .services-list {
    position: absolute; top: 168px; list-style: none;
  }
  .services-list li {
    position: absolute; white-space: nowrap;
    font-size: 10.5px; color: #e6efe4; line-height: 12.6px;
    padding-left: 12px;
  }
  .services-list li::before {
    content: ""; position: absolute; left: 0; top: 3px;
    border-left: 6px solid var(--green-light);
    border-top: 3.5px solid transparent; border-bottom: 3.5px solid transparent;
  }
</style>
</head>
<body>

<section class="card card--front">
  <div class="skyline" role="img" aria-label="Faint illustration of a house and city buildings"></div>

  <div class="brand">
    <span class="brand__name">VARKELT</span>
    <span class="brand__sub">CONSTRUCTION LTD</span>
  </div>

  <div class="divider"></div>

  <div class="person">
    <p class="person__name">Tomasz Brelwik</p>
    <p class="person__title">Managing Director</p>
  </div>

  <ul class="contacts">
    <li><svg viewBox="0 0 10 10"><path d="M2 0.5 L3.6 2.6 L2.8 3.6 Q4 6 6.4 7.2 L7.4 6.4 L9.5 8 L8.4 9.5 Q3.5 9 0.5 1.6 Z"/></svg>020 5194 6281</li>
    <li><svg viewBox="0 0 10 10"><path d="M2.5 0 H7.5 V10 H2.5 Z M3.5 1 V8 H6.5 V1 Z"/></svg>07845139072</li>
    <li><svg viewBox="0 0 10 10"><path d="M0 2 H10 V8.5 H0 Z M0.8 2.6 L5 5.6 L9.2 2.6 Z"/></svg>tomasz@varkelt.co.uk</li>
  </ul>

  <svg class="wave" viewBox="0 0 453 60" preserveAspectRatio="none">
    <path d="M0 22 C90 40 170 38 250 24 S390 -2 453 10 L453 60 L0 60 Z" fill="#ffffff"/>
    <path d="M0 25 C90 43 170 41 250 27 S390 1 453 13 L453 60 L0 60 Z" fill="var(--green-light)"/>
    <path d="M0 32 C90 46 170 44 250 31 S390 8 453 20 L453 60 L0 60 Z" fill="var(--green-dark)"/>
  </svg>
  <p class="website">www.<span>varkelt</span>.co.uk</p>
</section>

<section class="card card--back">
  <div class="brand">
    <span class="brand__name">VARKELT</span>
    <span class="brand__sub">CONSTRUCTION LTD</span>
  </div>

  <div class="services-rule"></div>
  <div class="services-band"></div>
  <div class="services-tab">SERVICES</div>

  <ul class="services-list">
    <li style="left:40px;top:0">Kitchen Renovations</li>
    <li style="left:40px;top:12.6px">Bathroom Renovations</li>
    <li style="left:40px;top:25.2px">House Renovations</li>
    <li style="left:40px;top:37.8px">Garage Conversions</li>
    <li style="left:40px;top:50.4px">Extensions</li>
    <li style="left:187px;top:0">Plumbing &amp; Heating</li>
    <li style="left:187px;top:12.6px">Bricklaying</li>
    <li style="left:187px;top:25.2px">Landscaping</li>
    <li style="left:187px;top:37.8px">Decorating</li>
    <li style="left:187px;top:50.4px">Plastering</li>
    <li style="left:317px;top:0">Loft Conversions</li>
    <li style="left:317px;top:12.6px">Conservatories</li>
    <li style="left:317px;top:25.2px">Carpentry</li>
    <li style="left:317px;top:37.8px">Tiling</li>
    <li style="left:317px;top:50.4px">Electrical</li>
  </ul>
</section>

</body>
</html>
```